Verodex business card

Business card for sustainable investment company called "Verodex". Verodex is an exchange platform selling carbon credits between buyers and sellers. Carbon Credits are an environmental commodity for reducing global carbon emissions.

the card should obviously have our logo and the theme should be sustainability/environment mixed with a trading platform.

Contact Information for Business Card

Logo, Name, Title, Phone, Email

Colors
0054AA
0677BA
7BADD7
CADEEF
E8F1F8
0094D4
00A9DD
6FCCEA
C7EBF8
E9F6FB
00AB8E
00BBA5
67D7C9
C6EFE9
E9F9F6
59FF00
82FF00
B8FF75
E3FFCB
F4FFEA

```html
<!DOCTYPE html>
<html lang="en">
<head>
<meta charset="utf-8">
<title>Verodex Business Card</title>
<link rel="stylesheet" href="https://fonts.googleapis.com/css2?family=Poppins:wght@400;600&display=swap">
<style>
  :root {
    --page-bg: #e6e8ec;
    --card-frost: #f1ecec;
    --card-cyan: #33d9ef;
    --wave-blue: #1f7ee6;
    --ink-navy: #1f2b47;
    --mark-blue: #1fa8ee;
  }
  * { margin: 0; padding: 0; box-sizing: border-box; }
  html, body {
    width: 1200px; height: 900px; overflow: hidden;
    background: var(--page-bg);
    font-family: "Poppins", sans-serif;
  }
  .business-card {
    position: absolute; left: 100px; top: 140px;
    width: 1000px; height: 620px;
    background: var(--card-frost);
    overflow: hidden;
    box-shadow: 0 12px 40px rgba(30, 40, 60, 0.18);
  }
  .card-wave { position: absolute; inset: 0; width: 1000px; height: 620px; }
  .brand {
    position: absolute; left: 48px; top: 94px;
    display: flex; align-items: center; gap: 22px;
  }
  .brand-dot {
    width: 78px; height: 78px; border-radius: 50%;
    background: var(--mark-blue);
  }
  .brand-name {
    font-weight: 600; font-size: 54px; letter-spacing: 1px;
    color: var(--ink-navy); line-height: 1;
  }
  .person { position: absolute; left: 545px; top: 282px; color: var(--ink-navy); }
  .person-name { font-weight: 600; font-size: 41px; letter-spacing: 1px; line-height: 1.1; }
  .person-title { font-weight: 400; font-size: 29px; line-height: 1.2; }
  .contact-list {
    position: absolute; left: 545px; top: 408px;
    list-style: none; color: var(--ink-navy);
  }
  .contact-item {
    display: flex; align-items: center; gap: 10px;
    font-size: 30px; line-height: 37px;
  }
  .contact-icon { width: 26px; height: 26px; flex: none; }
</style>
</head>
<body>
  <div class="business-card">
    <svg class="card-wave" viewBox="0 0 1000 620" aria-hidden="true">
      <path d="M440,0 L481,0 C520,60 520,200 470,300 C430,380 400,470 430,560 C440,590 450,605 458,620 L440,620 C420,560 400,470 425,390 C450,300 500,190 440,0 Z" fill="var(--wave-blue)"/>
      <path d="M481,0 C520,60 520,200 470,300 C430,380 400,470 430,560 C440,590 450,605 458,620 L1000,620 L1000,0 Z" fill="var(--card-cyan)"/>
    </svg>

    <div class="brand">
      <span class="brand-dot"></span>
      <span class="brand-name">VERODEX</span>
    </div>

    <div class="person">
      <p class="person-name">MARCUS HALE</p>
      <p class="person-title">Managing Director</p>
    </div>

    <ul class="contact-list">
      <li class="contact-item">
        <svg class="contact-icon" viewBox="0 0 24 24" aria-hidden="true"><path d="M6.6 10.8a15.1 15.1 0 0 0 6.6 6.6l2.2-2.2a1 1 0 0 1 1-.25 11.4 11.4 0 0 0 3.6.57 1 1 0 0 1 1 1V20a1 1 0 0 1-1 1A17 17 0 0 1 3 4a1 1 0 0 1 1-1h3.5a1 1 0 0 1 1 1c0 1.25.2 2.45.57 3.57a1 1 0 0 1-.25 1z" fill="var(--ink-navy)"/></svg>
        <span>041-570 238 614</span>
      </li>
      <li class="contact-item">
        <svg class="contact-icon" viewBox="0 0 24 24" aria-hidden="true"><rect x="2" y="5" width="20" height="14" fill="var(--ink-navy)"/><path d="M2 5l10 8 10-8" fill="none" stroke="var(--card-cyan)" stroke-width="1.6"/></svg>
        <span>hello@verodex-mail.com</span>
      </li>
      <li class="contact-item">
        <svg class="contact-icon" viewBox="0 0 24 24" aria-hidden="true"><g fill="none" stroke="var(--ink-navy)" stroke-width="1.8"><circle cx="12" cy="12" r="9.5"/><ellipse cx="12" cy="12" rx="4.2" ry="9.5"/><path d="M2.5 12h19M4 7h16M4 17h16"/></g></svg>
        <span>www.verodex-trade.com</span>
      </li>
    </ul>
  </div>
</body>
</html>
```